Furniture & Lighting Wholesaler Needs a Product Catalogue/Look Book

Our company, Vostre Merchant Co, imports quality hand-made furniture, lighting and decor from South Africa. Our products are well-designed and are designed to be used in up-market hotels and homes. Our primary customers are small- to medium-size retail shops.
We require a +/- 14-16 page look book (concept as per attached image) that will be used both in hard-copy and online. We have all of the necessary high-res images, descriptions/text etc. We need you to propose several design concepts from which we can choose, and then execute the design.
Please visit our website www.vostremerchant.example to see the products and their descriptions, as well as to get a feel for our style. Thank you for looking at our project!
Target Market(s)
Boutique Furniture Stores; Interior Designers
Industry/Entity Type
It Company
Font styles to use
Other font styles liked:
- Bauer Bodini and Open Sans Condensed
Look and feel
Each slider illustrates characteristics of the customer's brand and the style your logo design should communicate.

```html
<!DOCTYPE html>
<html lang="en">
<head>
<meta charset="utf-8">
<title>Vostre Merchant Co – Look Book Spread</title>
<link href="https://fonts.googleapis.com/css2?family=Open+Sans:wght@400;600&display=swap" rel="stylesheet">
<style>
:root{
  --backdrop:#cbcbcb;
  --paper:#ffffff;
  --paper-shade:#eeeeee;
  --gold:#a49a74;
  --ink:#3c3c3c;
  --charcoal:#4a4a4a;
  --pill:#e4e4e4;
}
*{margin:0;padding:0;box-sizing:border-box}
html,body{width:1200px;height:800px;overflow:hidden;background:var(--backdrop);font-family:"Open Sans",sans-serif;color:var(--ink)}
.spread{position:absolute;left:50px;top:90px;width:1100px;height:620px;display:flex;box-shadow:0 10px 30px rgba(0,0,0,.18)}
.page{position:relative;width:550px;height:620px;background:var(--paper);overflow:hidden}
.page--left{background:linear-gradient(to right,var(--paper) 90%,var(--paper-shade))}
.page--right{background:linear-gradient(to left,var(--paper) 90%,var(--paper-shade))}
.section-title{position:absolute;color:var(--gold);font-weight:400;text-transform:uppercase;line-height:1.02;letter-spacing:.5px;white-space:nowrap}
.intro{position:absolute;color:var(--gold);font-weight:600;font-size:9px;line-height:1.4;text-transform:uppercase}
.column{position:absolute;font-size:8.5px;line-height:1.45;color:var(--ink)}
.column p{margin-bottom:8px}
.column .intro-inline{color:var(--gold);font-weight:600;text-transform:uppercase;font-size:9px;line-height:1.4}
.side-tab{position:absolute;width:34px;background:var(--gold)}
.page-number{position:absolute;width:34px;height:34px;background:var(--charcoal);color:#d8d8d8;font-size:10px;display:flex;align-items:center;justify-content:center}
.web-pill{position:absolute;height:22px;background:var(--pill);border-radius:11px;display:flex;align-items:center;gap:8px;padding:0 14px;font-size:8px;color:#6a6a6a}
.web-pill .square{width:10px;height:10px;border:2px solid var(--charcoal)}
.photo{position:absolute;border-radius:14px;background:linear-gradient(135deg,#eeebe6,#cdbba7 55%,#7a6656)}
.map{position:absolute;border-radius:40%;background:linear-gradient(90deg,#8a8a8a,#5e5e5e 55%,#9a9a9a)}
</style>
</head>
<body>
<main class="spread">
  <section class="page page--left">
    <h2 class="section-title" style="left:50px;top:260px;font-size:30px">After Sales<br>Service</h2>
    <p class="intro" style="left:50px;top:336px;width:180px">Our team stays with you well after delivery, helping with care, repairs and any question about your pieces.</p>
    <div class="column" style="left:50px;top:400px;width:180px">
      <p>Every order is followed up by a dedicated contact who knows your account, your stock and the pieces you have placed in your store.</p>
      <p>Replacement parts ship within days.</p>
      <p>Our craftsmen can refinish timber, rewire lamps and restore woven detail so each item keeps its hand-made character for years of use in busy hotel lobbies and homes.</p>
    </div>
    <div class="column" style="left:255px;top:200px;width:140px">
      <p>Ask for a visit and we will come to you.</p>
      <p class="intro-inline">We offer training for your sales staff, care guides for every range and a direct line to our workshop team in South Africa.</p>
      <p>Trade customers receive priority support and clear answers on lead times, stock levels and custom sizes.</p>
      <p>Speak to us about any piece, any time.</p>
    </div>
    <div class="photo" role="img" aria-label="Photo of smiling customer service staff wearing headsets" style="left:408px;top:200px;width:132px;height:112px"></div>
    <div class="side-tab" style="left:0;top:400px;height:220px;border-radius:0 24px 0 0"></div>
    <div class="page-number" style="left:0;bottom:0">14</div>
    <div class="web-pill" style="right:30px;bottom:20px"><span class="square"></span>www.vostremerchant.example</div>
  </section>
  <section class="page page--right">
    <h2 class="section-title" style="left:40px;top:90px;font-size:30px">Worldwide<br>Distribution<br>Service</h2>
    <p class="intro" style="left:40px;top:200px;width:190px">From our workshops to your showroom, we manage freight, customs and insurance for every order we send.</p>
    <div class="column" style="left:40px;top:266px;width:190px">
      <p>We ship by sea and air to retailers across Europe, the Americas and Asia, packing each item by hand for a safe arrival.</p>
      <p>Consolidated loads keep costs low for smaller stores.</p>
      <p>Track each shipment online and receive updates until delivery.</p>
    </div>
    <div class="column" style="left:255px;top:190px;width:180px">
      <p>Orders leave weekly from Cape Town.</p>
      <p class="intro-inline">Door to door service is available in more than forty countries with one simple invoice.</p>
      <p>Our logistics team plans every route and handles paperwork so you can focus on your customers.</p>
      <p>Ask about sample shipments.</p>
    </div>
    <div class="map" role="img" aria-label="Dotted world map" style="left:320px;top:50px;width:170px;height:85px"></div>
    <div class="side-tab" style="right:0;top:0;height:210px;border-radius:0 0 0 24px"></div>
    <div class="page-number" style="right:0;top:176px">15</div>
    <div class="web-pill" style="left:30px;bottom:20px"><span class="square"></span>www.vostremerchant.example</div>
  </section>
</main>
</body>
</html>
```